Business Card Design (NEW FILES)

ATTENTION: New vector files are available. Please update your design to reflect/use the new (better resolution) logo images.

Seeking a unique and professional business card design for a commercial drone photography/videography business. The layout should feature
the logo (attached) and include the following information:
Owen Tarrick
614-502-7738
www.skylarkreelworks.example
NRD Certified Remote Pilot

Owen Tarrick

```html
<!DOCTYPE html>
<html lang="en">
<head>
<meta charset="utf-8">
<title>Skylark Reelworks – Business Card</title>
<link rel="stylesheet" href="https://fonts.googleapis.com/css2?family=Open+Sans:wght@400;600;700;800&display=swap">
<style>
  :root {
    --backdrop: #232323;
    --card: #ffffff;
    --navy: #1b1f4a;
    --orange: #ee8c4e;
    --shadow: rgba(0, 0, 0, 0.55);
  }
  * { box-sizing: border-box; margin: 0; padding: 0; }
  html, body {
    width: 1200px;
    height: 780px;
    overflow: hidden;
    background: var(--backdrop);
    font-family: "Open Sans", sans-serif;
  }
  .stage {
    width: 1200px;
    height: 780px;
    display: flex;
    align-items: center;
    justify-content: center;
    gap: 44px;
  }
  .card {
    position: relative;
    width: 540px;
    height: 309px;
    background: var(--card);
    box-shadow: 0 14px 30px var(--shadow);
  }
  .brand {
    display: flex;
    align-items: center;
    gap: 10px;
    color: var(--navy);
    font-weight: 700;
    white-space: nowrap;
  }
  .brand-dot {
    flex: none;
    border-radius: 50%;
    background: var(--orange);
  }
  .card-front {
    display: flex;
    align-items: center;
    justify-content: center;
  }
  .card-front .brand { font-size: 36px; letter-spacing: 0.5px; }
  .card-front .brand-dot { width: 22px; height: 22px; }

  .card-back .brand {
    position: absolute;
    left: 30px;
    top: 130px;
    font-size: 19px;
  }
  .card-back .brand-dot { width: 13px; height: 13px; }
  .divider {
    position: absolute;
    left: 262px;
    top: 52px;
    width: 1px;
    height: 126px;
    background: var(--orange);
  }
  .contact {
    position: absolute;
    left: 288px;
    top: 46px;
    color: var(--navy);
  }
  .person-name {
    font-size: 27px;
    font-weight: 800;
    line-height: 1.05;
  }
  .person-name .first { color: var(--orange); }
  .person-role {
    font-size: 12px;
    font-weight: 600;
    margin-top: 2px;
    margin-bottom: 14px;
  }
  .contact-list { list-style: none; }
  .contact-list li {
    display: flex;
    align-items: center;
    gap: 8px;
    font-size: 12.5px;
    line-height: 1;
    margin-bottom: 8px;
  }
  .contact-list svg { width: 12px; height: 12px; flex: none; }
  .credentials {
    position: absolute;
    left: 250px;
    right: 20px;
    bottom: 34px;
    text-align: center;
    color: var(--navy);
    font-size: 13.5px;
    font-weight: 600;
    line-height: 1.35;
  }
</style>
</head>
<body>
<main class="stage">
  <section class="card card-front" aria-label="Business card front">
    <div class="brand"><span class="brand-dot"></span>Skylark Reelworks</div>
  </section>

  <section class="card card-back" aria-label="Business card back">
    <div class="brand"><span class="brand-dot"></span>Skylark Reelworks</div>
    <div class="divider"></div>
    <div class="contact">
      <p class="person-name"><span class="first">Owen</span> Tarrick</p>
      <p class="person-role">Owner</p>
      <ul class="contact-list">
        <li>
          <svg viewBox="0 0 24 24" aria-hidden="true"><path fill="var(--orange)" d="M6.6 10.8a15.1 15.1 0 0 0 6.6 6.6l2.2-2.2a1 1 0 0 1 1-.25 11.4 11.4 0 0 0 3.6.57 1 1 0 0 1 1 1V20a1 1 0 0 1-1 1A17 17 0 0 1 3 4a1 1 0 0 1 1-1h3.5a1 1 0 0 1 1 1c0 1.25.2 2.45.57 3.57a1 1 0 0 1-.25 1z"/></svg>
          614-502-7738
        </li>
        <li>
          <svg viewBox="0 0 24 24" aria-hidden="true"><circle cx="12" cy="12" r="10" fill="none" stroke="var(--orange)" stroke-width="2.4"/><ellipse cx="12" cy="12" rx="4.2" ry="10" fill="none" stroke="var(--orange)" stroke-width="2"/><path d="M2 12h20" stroke="var(--orange)" stroke-width="2"/></svg>
          www.skylarkreelworks.example
        </li>
        <li>
          <svg viewBox="0 0 24 24" aria-hidden="true"><rect x="2" y="5" width="20" height="14" rx="1.5" fill="var(--orange)"/><path d="M3 6l9 7 9-7" fill="none" stroke="#fff" stroke-width="1.8"/></svg>
          info@skylarkreelworks.example
        </li>
      </ul>
    </div>
    <p class="credentials">NRD Certified Remote Pilot<br>Fully Insured</p>
  </section>
</main>
</body>
</html>
```